Corporate Business Card

Very professional, Modern, Not to busy, include phone address email, website
(503) 617-4930, 18761 52nd Avenue S, Salem, OR 98047, martin@plumlinegroup.com, varkoworks.com

Target Market(s)

Manufacturing

Industry/Entity Type

Aero, machining, manufacturing, Off road racing

Contact Information for Business Card

Phone, address email, website

```html
<!DOCTYPE html>
<html lang="en">
<head>
<meta charset="utf-8">
<title>Varko Industries – Business Card</title>
<link href="https://fonts.googleapis.com/css2?family=Montserrat:wght@400;600;700&family=Roboto:wght@400&display=swap" rel="stylesheet">
<style>
  :root {
    --navy: #17336e;
    --red: #d2232a;
    --paper: #f7f7f7;
    --ink: #2b2b2b;
    --stage: #e4e5e8;
  }
  * { box-sizing: border-box; margin: 0; padding: 0; }
  html, body { width: 1200px; height: 900px; overflow: hidden; }
  body {
    background: var(--stage);
    font-family: "Montserrat", sans-serif;
    display: flex;
    flex-direction: column;
    align-items: center;
    justify-content: center;
    gap: 40px;
  }
  .card {
    position: relative;
    width: 700px;
    height: 400px;
    border-radius: 22px;
    overflow: hidden;
    box-shadow: 0 6px 18px rgba(0,0,0,.12);
  }
  .card--back { background: var(--navy); }
  .card--front { background: var(--paper); }

  .brand {
    position: absolute;
    display: flex;
    align-items: center;
    gap: 16px;
    font-family: "Montserrat", sans-serif;
    font-weight: 700;
    letter-spacing: 1px;
  }
  .brand__mark { width: 22px; height: 22px; background: var(--red); }
  .card--back .brand { left: 0; right: 0; top: 165px; justify-content: center; font-size: 50px; color: #fff; }
  .card--front .brand { left: 0; right: 0; top: 60px; justify-content: center; font-size: 46px; color: var(--navy); }

  .person {
    position: absolute;
    right: 370px;
    top: 205px;
    text-align: right;
  }
  .person__name { font-size: 28px; font-weight: 700; letter-spacing: 1px; color: var(--navy); }
  .person__name .surname { color: var(--red); }
  .person__role { font-size: 19px; font-weight: 400; color: var(--ink); margin-top: 2px; }

  .divider {
    position: absolute;
    left: 350px;
    top: 200px;
    width: 2px;
    height: 90px;
    background: var(--navy);
  }

  .contact {
    position: absolute;
    left: 372px;
    top: 205px;
    list-style: none;
    font-family: "Roboto", sans-serif;
    font-size: 17px;
    color: var(--ink);
  }
  .contact li { display: flex; align-items: center; gap: 10px; height: 26px; }
  .contact svg { width: 14px; height: 14px; fill: var(--red); flex: none; }

  .footer-bands { position: absolute; left: 0; bottom: 0; width: 700px; height: 110px; }
  .address {
    position: absolute;
    left: 40px;
    top: 302px;
    height: 42px;
    line-height: 42px;
    color: #fff;
    font-family: "Roboto", sans-serif;
    font-size: 18px;
    letter-spacing: .3px;
  }
</style>
</head>
<body>

  <section class="card card--back">
    <div class="brand"><span class="brand__mark"></span>Varko Industries</div>
  </section>

  <section class="card card--front">
    <div class="brand"><span class="brand__mark"></span>Varko Industries</div>

    <div class="person">
      <div class="person__name">OWEN <span class="surname">HARTLEY</span></div>
      <div class="person__role">Owner</div>
    </div>

    <div class="divider"></div>

    <ul class="contact">
      <li>
        <svg viewBox="0 0 24 24"><path d="M6.6 10.8a15.1 15.1 0 0 0 6.6 6.6l2.2-2.2a1 1 0 0 1 1-.25 11.4 11.4 0 0 0 3.6.57 1 1 0 0 1 1 1V20a1 1 0 0 1-1 1A17 17 0 0 1 3 4a1 1 0 0 1 1-1h3.5a1 1 0 0 1 1 1c0 1.25.2 2.45.57 3.57a1 1 0 0 1-.25 1z"/></svg>
        (503) 617-4930
      </li>
      <li>
        <svg viewBox="0 0 24 24"><path d="M2 5h20v2l-10 6L2 7zm0 4l10 6 10-6v10H2z"/></svg>
        martin@plumlinegroup.com
      </li>
      <li>
        <svg viewBox="0 0 24 24"><path d="M12 2a10 10 0 1 0 0 20 10 10 0 0 0 0-20zm6.9 6h-2.9a15.6 15.6 0 0 0-1.4-3.6A8 8 0 0 1 18.9 8zM12 4a14 14 0 0 1 1.9 4h-3.8A14 14 0 0 1 12 4zM4.3 14a8 8 0 0 1 0-4h3.4a16 16 0 0 0 0 4zm.8 2h2.9a15.6 15.6 0 0 0 1.4 3.6A8 8 0 0 1 5.1 16zM8 8H5.1a8 8 0 0 1 4.3-3.6A15.6 15.6 0 0 0 8 8zm4 12a14 14 0 0 1-1.9-4h3.8A14 14 0 0 1 12 20zm2.3-6H9.7a14.7 14.7 0 0 1 0-4h4.6a14.7 14.7 0 0 1 0 4zm.3 5.6A15.6 15.6 0 0 0 16 16h2.9a8 8 0 0 1-4.3 3.6zM16.3 14a16 16 0 0 0 0-4h3.4a8 8 0 0 1 0 4z"/></svg>
        www.varkoworks.com
      </li>
    </ul>

    <svg class="footer-bands" viewBox="0 0 700 110" aria-hidden="true">
      <polygon points="0,12 590,12 560,54 0,54" fill="var(--navy)"/>
      <polygon points="600,44 700,44 700,90 560,90" fill="var(--red)"/>
    </svg>
    <div class="address">18761 52nd Avenue S, Salem, OR 98047</div>
  </section>

</body>
</html>
```